BWP Business Card

A double sided business card based on your "Brindlewood Partners Ltd" Logo. To use the "BWP" logo on 1 side and the full company logo on the reverse.

Detials to be included:

Name: Tomas Wheeler
Postion: Consultant Orthotist & Expert Witness
T: +44 (0) 7700 938271
F: +44 (0) 7654 8820

```html
<!DOCTYPE html>
<html lang="en">
<head>
<meta charset="utf-8">
<title>BWP Business Card</title>
<link href="https://fonts.googleapis.com/css2?family=Cinzel:wght@600&family=Open+Sans:wght@400;700&display=swap" rel="stylesheet">
<style>
  :root {
    --navy: #0f3a6e;
    --grey: #9a9b9d;
    --text: #3b3d40;
    --card: #ffffff;
    --backdrop: #eceae6;
    --rule: #c9c9cb;
  }
  * { box-sizing: border-box; margin: 0; padding: 0; }
  html, body { width: 1200px; height: 720px; overflow: hidden; }
  body {
    background: var(--backdrop);
    font-family: "Open Sans", Arial, sans-serif;
    display: flex;
    align-items: center;
    justify-content: center;
    gap: 40px;
  }
  .card {
    position: relative;
    width: 540px;
    height: 309px;
    background: var(--card);
    box-shadow: 0 2px 10px rgba(0,0,0,.12);
    overflow: hidden;
  }

  /* Front side */
  .brand {
    position: absolute;
    left: 30px;
    top: 34px;
    display: flex;
    align-items: center;
    gap: 14px;
  }
  .brand-square {
    width: 44px;
    height: 44px;
    background: var(--navy);
  }
  .brand-rule {
    width: 1px;
    height: 62px;
    background: var(--rule);
  }
  .brand-name {
    font-family: "Cinzel", Georgia, serif;
    font-weight: 600;
    color: var(--navy);
    font-size: 21px;
    line-height: 1.1;
  }
  .brand-tagline {
    margin-top: 6px;
    padding-top: 4px;
    border-top: 1px solid var(--rule);
    font-family: "Cinzel", Georgia, serif;
    font-size: 9px;
    letter-spacing: .5px;
    color: var(--navy);
  }
  .holder {
    position: absolute;
    right: 30px;
    top: 126px;
    text-align: right;
  }
  .holder-name {
    font-weight: 700;
    font-size: 17px;
    color: var(--navy);
  }
  .holder-role {
    font-size: 12px;
    color: var(--grey);
    margin-top: 4px;
  }
  .tab-grey {
    position: absolute;
    right: -6px;
    top: 120px;
    width: 14px;
    height: 30px;
    border-radius: 7px;
    background: var(--grey);
  }
  .tab-navy {
    position: absolute;
    left: -6px;
    top: 206px;
    width: 14px;
    height: 70px;
    border-radius: 7px;
    background: var(--navy);
  }
  .contact {
    position: absolute;
    left: 30px;
    top: 200px;
    list-style: none;
    font-size: 12px;
    color: var(--text);
  }
  .contact li {
    display: flex;
    align-items: center;
    gap: 8px;
    height: 19px;
  }
  .contact svg { width: 12px; height: 12px; fill: var(--navy); flex: none; }
  .contact .address { padding-left: 0; margin-top: 4px; }

  /* Back side */
  .card-back {
    display: flex;
    align-items: center;
    justify-content: center;
    gap: 22px;
  }
  .back-square {
    width: 64px;
    height: 64px;
    background: var(--navy);
  }
  .back-mark {
    font-family: "Cinzel", Georgia, serif;
    font-weight: 600;
    font-size: 92px;
    letter-spacing: 6px;
    color: var(--navy);
    line-height: 1;
  }
</style>
</head>
<body>

  <section class="card card-front" aria-label="Business card front">
    <div class="brand">
      <div class="brand-square"></div>
      <div class="brand-rule"></div>
      <div>
        <div class="brand-name">Brindlewood<br>Partners Ltd</div>
        <div class="brand-tagline">Excellence in Medical Legal Reporting</div>
      </div>
    </div>

    <div class="tab-grey"></div>
    <div class="holder">
      <div class="holder-name">Tomas Wheeler</div>
      <div class="holder-role">Consultant Orthotist &amp; Expert Witness</div>
    </div>

    <div class="tab-navy"></div>
    <ul class="contact">
      <li>
        <svg viewBox="0 0 24 24" aria-hidden="true"><path d="M6.6 10.8a15 15 0 0 0 6.6 6.6l2.2-2.2c.3-.3.7-.4 1-.2 1.1.4 2.3.6 3.6.6.6 0 1 .4 1 1V20c0 .6-.4 1-1 1A17 17 0 0 1 3 4c0-.6.4-1 1-1h3.5c.6 0 1 .4 1 1 0 1.3.2 2.5.6 3.6.1.3 0 .7-.2 1z"/></svg>
        +44 (0) 7700 938271
      </li>
      <li>
        <svg viewBox="0 0 24 24" aria-hidden="true"><path d="M7 3h10v5H7zM4 9h16a2 2 0 0 1 2 2v6h-4v4H6v-4H2v-6a2 2 0 0 1 2-2zm4 7v3h8v-3z"/></svg>
        +44 (0) 7654 8820
      </li>
      <li>
        <svg viewBox="0 0 24 24" aria-hidden="true"><path d="M2 5h20v14H2zm2 2v.5l8 5 8-5V7zm0 2.8V17h16V9.8l-8 5z"/></svg>
        tomas@brindlewoodpartners.co.uk
      </li>
      <li class="address">18 Alder Row Kingsford, Surrey, KF4 2RN</li>
    </ul>
  </section>

  <section class="card card-back" aria-label="Business card back">
    <div class="back-square"></div>
    <div class="back-mark">BWP</div>
  </section>

</body>
</html>
```